Commercial Cleaning Company Website Design

We are working with Harbor Tidy Team. They are a commercial cleaning company that needs a new website design.

Some sites to use for inspiration:

https://www.plenvask.com
https://gleam-panecare.com
https://tidwellhelpers.net
https://quietnesthouse.com
https://www.thedustingbureau.com
https://www.pennytidy.com

Thank you for taking the time to consider designing a website for us. We are web developers based in Stockton and Los Angeles, CA, USA. Most of our projects go through the same process. Understanding this process may help you win a project with us. We custom-code all of our websites in-house. We don’t have any requirements as to what tools you use for your design, but we prefer Figma files. For any design that we label as four-stars, we send it to the client for review. The client picks the final design they want us to use. Once we complete this process, we will continue to show additional clients all the four-star sites and purchase them later. Your designs will have multiple chances to sell. For better chances of success, we ask that you follow these guidelines.

IMAGES:
If you use any images or icons in the design, we ask that you have a link to the asset so we can purchase the image/icon. Most of the designs we submit do not have the customer’s images on them unless they have some great images. Be creative; show us the feeling you are trying to portray with your image choices. Use any royalty-free site you choose. We subscribe to Adobe and mainly use their images, but we can purchase images outside of Adobe.

PLEASE NOTE: we will not submit designs to clients with watermarks on the images.

FONTS:
We ask that you identify the fonts used in the design. This can be done in a message if you want. We typically use Google Fonts and Adobe Fonts.

CONTENT:
We're always open to different content and ideas. We often submit designs with stock images so the client can see our vision. We typically take pictures after the website launch to use their images with our vision. Lorem Ipsum is fine for paragraphs, but we ask that you write the headers in correct English. We want to be able to show the vision and identify the sections of the website.

INSPIRATION:
We typically add a couple of links in the brief of websites we like to help you get started in your design.

REVISIONS:
We do not often ask for revisions of the designs unless we see something in the design that may not appeal to the client. If there are slight changes that we want to make, we do that in the development process.

FEEDBACK:
We rarely give feedback on designs during the design process. We are working on many website projects and do not have the time to provide feedback. We usually respond if your request is well thought out and asks specific questions, but a note asking “feedback, please” usually goes unanswered.

```html
<!DOCTYPE html>
<html lang="en">
<head>
<meta charset="utf-8">
<title>Harbor Tidy Team</title>
<link rel="stylesheet" href="https://fonts.googleapis.com/css2?family=Montserrat:wght@400;500;600;700&display=swap">
<style>
:root{
  --blue:#1f4fc1;
  --blue-dark:#1a46b0;
  --blue-soft:#eef3fb;
  --ink:#1b1f2a;
  --muted:#555b66;
  --line:#b9c3d6;
  --white:#ffffff;
  --star:#f5a623;
}
*{box-sizing:border-box;margin:0;padding:0}
html,body{width:1200px;height:3693px;overflow:hidden}
body{position:relative;font-family:"Montserrat",sans-serif;color:var(--ink);background:var(--white)}
.abs{position:absolute}
.hero{left:0;top:0;width:1200px;height:585px;background:linear-gradient(100deg,#2552c4 0%,#2e5fcf 55%,#2a59c9 100%)}
.hero-photo{left:724px;top:115px;width:380px;height:470px;border-radius:190px 190px 0 0;background:linear-gradient(180deg,#c9a486 0%,#e8e2db 40%,#3a64c4 75%,#2d55b8 100%)}
.topbar{left:0;top:0;width:1200px;height:100px;border-bottom:1px solid rgba(255,255,255,.35)}
.brand{left:112px;top:30px;display:flex;align-items:center;gap:12px;color:var(--white);font-weight:600;font-size:22px;letter-spacing:3px}
.brand-dot{width:18px;height:18px;border-radius:50%;background:var(--white)}
.nav{left:493px;top:36px;display:flex;gap:33px;color:rgba(255,255,255,.85);font-size:16px}
.nav .active{color:var(--white);font-weight:700}
.btn-contact{left:966px;top:30px;width:122px;height:35px;border-radius:8px;background:var(--white);color:var(--blue);font-size:15px;font-weight:600;display:flex;align-items:center;justify-content:center}
.hero-title{left:111px;top:212px;color:var(--white);font-size:46px;line-height:59px}
.hero-title b{font-weight:700}
.hero-title span{font-weight:400}
.hero-sub{left:111px;top:336px;color:var(--white);font-size:16px;line-height:26px;width:470px}
.btn-start{left:110px;top:413px;width:122px;height:35px;border-radius:8px;background:var(--white);color:var(--blue);font-size:15px;font-weight:600;display:flex;align-items:center;justify-content:center}
.sec-title{width:1200px;left:0;text-align:center;color:var(--blue);font-size:37px;letter-spacing:.5px}
.sec-title b{font-weight:700}
.sec-title span{font-weight:400}
.sec-text{left:200px;width:800px;text-align:center;color:var(--muted);font-size:15.5px;line-height:24px}
.card{width:308px;height:274px;border-radius:12px;overflow:hidden}
.card-label{position:absolute;left:32px;right:32px;bottom:-14px;height:40px;background:var(--white);border-radius:12px 12px 0 0;color:var(--blue);font-size:17px;font-weight:500;text-align:center;padding-top:8px}
.arrow{width:46px;height:46px;border-radius:50%;display:flex;align-items:center;justify-content:center}
.arrow.outline{border:2px solid var(--blue)}
.arrow.solid{background:var(--blue)}
.about-bg{left:0;top:1197px;width:1200px;height:650px;background:var(--blue-soft)}
.about-photo{left:130px;top:1276px;width:440px;height:500px;border-radius:16px;background:radial-gradient(ellipse at 50% 60%,#3f7de0 0%,#8fb2ea 45%,#eef3fb 75%)}
.left-title{color:var(--blue);font-size:37px}
.left-title b{font-weight:700}
.left-title span{font-weight:400}
.feature{left:619px;width:469px;height:117px;border:1px solid var(--line);border-radius:12px;display:flex;align-items:center;padding:0 20px}
.feature svg{flex:none}
.feature h3{font-size:20px;font-weight:500;margin-bottom:10px}
.feature p{font-size:13px;line-height:20px;color:var(--muted)}
.feature .txt{margin-left:40px}
.btn-blue{background:var(--blue);color:var(--white);border-radius:8px;font-size:15px;font-weight:600;display:flex;align-items:center;justify-content:center}
.partners{left:112px;top:2010px;width:976px;display:flex;justify-content:space-between;align-items:center}
.partner-badge{width:110px;height:28px;border-radius:4px;background:#c8ccd4}
.dots{left:0;width:1200px;display:flex;justify-content:center;gap:9px;align-items:center}
.dots i{width:9px;height:9px;border-radius:50%;background:#4d5564;display:block}
.dots i.on{width:14px;height:14px;background:var(--blue)}
.step{left:112px;width:530px;height:115px;background:var(--blue-soft);border-radius:12px;display:flex;align-items:center;padding-left:28px}
.step .bar{width:2px;height:66px;background:var(--blue);margin:0 18px 0 24px}
.step h3{font-size:22px;font-weight:500;margin-bottom:10px}
.step p{font-size:13px;line-height:20px;color:var(--muted)}
.process-circle{left:774px;top:2121px;width:304px;height:304px;border-radius:50%;background:#e3e9f5}
.process-photo{left:770px;top:2130px;width:370px;height:565px;border-radius:150px 150px 20px 20px;background:linear-gradient(180deg,#c9a486 0%,#2b2f36 30%,#3c424b 80%,#7a8290 100%)}
.testi-bg{left:0;top:2778px;width:1200px;height:661px;background:var(--blue-soft)}
.tcard{top:3016px;width:297px;height:292px;border:1px solid var(--line);border-radius:12px;background:var(--blue-soft);padding:26px 22px 0 22px}
.tcard .head{display:flex;justify-content:space-between;align-items:center;margin-bottom:20px}
.quote{color:var(--blue);font-size:44px;font-weight:700;line-height:24px;height:24px;font-family:Georgia,serif}
.stars{color:var(--star);font-size:13px;letter-spacing:1px}
.tcard p{font-size:12px;line-height:20.5px;color:var(--muted)}
.person{display:flex;align-items:center;gap:14px;margin-top:20px}
.avatar{width:46px;height:46px;border-radius:50%;background:var(--blue);color:var(--white);font-size:20px;font-weight:600;display:flex;align-items:center;justify-content:center}
.person h4{font-size:15px;font-weight:500}
.person small{font-size:11px;color:var(--muted)}
.footer{left:0;top:3439px;width:1200px;height:254px;background:var(--blue)}
.footer-brand{left:0;width:1200px;top:3505px;text-align:center;color:var(--white);font-size:26px;font-weight:600;letter-spacing:4px}
.footer-nav{left:0;width:1200px;top:3591px;display:flex;justify-content:center;gap:36px;color:var(--white);font-size:18px}
.footer-line{left:112px;top:3630px;width:976px;height:1px;background:rgba(255,255,255,.45)}
.copyright{left:0;width:1200px;top:3645px;text-align:center;color:var(--white);font-size:13px}
</style>
</head>
<body>

<!-- Hero -->
<section class="abs hero" aria-label="Hero">
  <div class="abs hero-photo" role="img" aria-label="Smiling cleaner in blue overalls and yellow gloves holding spray bottle"></div>
  <header class="abs topbar">
    <div class="abs brand"><span class="brand-dot"></span>HARBOR TIDY TEAM</div>
    <nav class="abs nav"><span class="active">Home</span><span>About</span><span>Services</span><span>Gallery</span><span>Testimonials</span></nav>
    <div class="abs btn-contact">Contact Us</div>
  </header>
  <h1 class="abs hero-title"><b>CLEANER WORKSPACES,</b><br><span>GREENER FUTURE.</span></h1>
  <p class="abs hero-sub">Creating clean, healthy, and productive environments for businesses of every size.</p>
  <div class="abs btn-start">Get Started</div>
</section>

<!-- Services -->
<h2 class="abs sec-title" style="top:660px"><b>OUR</b> <span>SERVICES</span></h2>
<p class="abs sec-text" style="top:725px">Lorem ipsum dolor sit amet, consectetur adipiscing elit, sed do eiusmod tempor incididunt ut labore et dolore magna aliqua. Quis ipsum suspendisse ultrices gravida.</p>
<div class="abs arrow outline" style="left:46px;top:930px"><svg width="18" height="18" viewBox="0 0 18 18"><path d="M11 3 5 9l6 6" fill="none" stroke="#1f4fc1" stroke-width="2" stroke-linecap="round"/></svg></div>
<div class="abs arrow solid" style="left:1110px;top:930px"><svg width="18" height="18" viewBox="0 0 18 18"><path d="m7 3 6 6-6 6" fill="none" stroke="#fff" stroke-width="2" stroke-linecap="round"/></svg></div>
<div class="abs card" style="left:112px;top:816px"><div style="width:100%;height:100%;background:linear-gradient(160deg,#e9e6e1,#bdb8b0 60%,#d8c44a)" role="img" aria-label="Worker mopping an office floor"></div><div class="card-label">Office Cleaning</div></div>
<div class="abs card" style="left:445px;top:816px"><div style="width:100%;height:100%;background:linear-gradient(160deg,#dfe6ee,#b9c4d0 55%,#6d737b)" role="img" aria-label="Floor scrubbing machine in a commercial lobby"></div><div class="card-label">Commercial Cleaning</div></div>
<div class="abs card" style="left:777px;top:816px"><div style="width:100%;height:100%;background:linear-gradient(160deg,#3b6fd8,#b8c3cf 55%,#e3e6ea)" role="img" aria-label="Gloved hands squeegeeing a window"></div><div class="card-label">Window &amp; Glass Cleaning</div></div>

<!-- About -->
<div class="abs about-bg"></div>
<div class="abs about-photo" role="img" aria-label="Cleaning cart with supplies, mop and caution sign"></div>
<h2 class="abs left-title" style="left:619px;top:1275px"><b>ABOUT</b> <span>US</span></h2>
<p class="abs" style="left:619px;top:1337px;width:470px;font-size:15.5px;line-height:24px;color:var(--muted)">Lorem ipsum dolor sit amet, consectetur adipiscing elit, sed do eiusmod tempor incididunt ut labore et dolore magna aliqua. Quis ipsum suspendisse ultrices gravida.</p>
<div class="abs feature" style="top:1451px">
  <svg width="64" height="64" viewBox="0 0 64 64" fill="none" stroke="#1f4fc1" stroke-width="2"><circle cx="30" cy="30" r="20"/><circle cx="30" cy="24" r="6"/><path d="M20 40c2-6 6-8 10-8s8 2 10 8"/><circle cx="44" cy="44" r="9"/><path d="m40 44 3 3 5-6"/></svg>
  <div class="txt"><h3>Shine Experts</h3><p>Lorem ipsum dolor sit amet, consectetur adipiscing elit, sed do eiusmod tempor</p></div>
</div>
<div class="abs feature" style="top:1585px">
  <svg width="64" height="64" viewBox="0 0 64 64" fill="none" stroke="#1f4fc1" stroke-width="2" stroke-linejoin="round"><path d="M22 50 14 34l6-2 6 8V14a3 3 0 0 1 6 0v16-20a3 3 0 0 1 6 0v20-16a3 3 0 0 1 6 0v18-12a3 3 0 0 1 6 0v18c0 10-6 16-14 16H30z"/><path d="M8 14h6M11 11v6M50 6v6M47 9h6"/></svg>
  <div class="txt"><h3>Spotless Touch</h3><p>Lorem ipsum dolor sit amet, consectetur adipiscing elit, sed do eiusmod tempor</p></div>
</div>
<div class="abs btn-blue" style="left:619px;top:1727px;width:122px;height:35px">Read More</div>

<!-- Partners -->
<h2 class="abs sec-title" style="top:1923px"><b>OUR</b> <span>PARTNER</span></h2>
<div class="abs partners">
  <div class="partner-badge"></div><div class="partner-badge"></div><div class="partner-badge" style="background:#9aa0aa"></div><div class="partner-badge"></div><div class="partner-badge" style="background:#9aa0aa"></div><div class="partner-badge"></div>
</div>
<div class="abs dots" style="top:2082px"><i class="on"></i><i></i><i></i><i></i></div>

<!-- Process -->
<h2 class="abs left-title" style="left:112px;top:2177px"><b>SIMPLE</b> <span>3 STEP PROCESS</span></h2>
<p class="abs" style="left:112px;top:2248px;width:630px;font-size:15.5px;line-height:24px;color:var(--muted)">Lorem ipsum dolor sit amet, consectetur adipiscing elit, sed do eiusmod tempor incididunt ut labore et dolore magna aliquauis</p>
<div class="abs process-circle"></div>
<div class="abs process-photo" role="img" aria-label="Cleaner in black uniform pushing a floor scrubber"></div>

<div class="abs step" style="top:2320px">
  <svg width="62" height="62" viewBox="0 0 62 62"><circle cx="34" cy="36" r="16" fill="#6f9ff0"/><circle cx="20" cy="28" r="8" fill="#2f66d8"/><circle cx="40" cy="18" r="6" fill="#2f66d8"/><circle cx="26" cy="44" r="6" fill="#a9c6f6"/><path d="M8 46h6M11 43v6M52 10h6M55 7v6" stroke="#1f4fc1" stroke-width="2"/></svg>
  <span class="bar"></span><div><h3>Book Your Package</h3><p>Lorem ipsum dolor sit amet, consectetur adipiscing elit,<br>sed do eiusmod tempor incididunt</p></div>
</div>
<div class="abs step" style="top:2449px">
  <svg width="62" height="62" viewBox="0 0 62 62"><circle cx="34" cy="36" r="16" fill="#6f9ff0"/><circle cx="20" cy="28" r="8" fill="#2f66d8"/><circle cx="40" cy="18" r="6" fill="#2f66d8"/><circle cx="26" cy="44" r="6" fill="#a9c6f6"/><path d="M8 46h6M11 43v6M52 10h6M55 7v6" stroke="#1f4fc1" stroke-width="2"/></svg>
  <span class="bar"></span><div><h3>Set the Schedule</h3><p>Lorem ipsum dolor sit amet, consectetur adipiscing elit,<br>sed do eiusmod tempor incididunt</p></div>
</div>
<div class="abs step" style="top:2577px">
  <svg width="62" height="62" viewBox="0 0 62 62"><circle cx="34" cy="36" r="16" fill="#6f9ff0"/><circle cx="20" cy="28" r="8" fill="#2f66d8"/><circle cx="40" cy="18" r="6" fill="#2f66d8"/><circle cx="26" cy="44" r="6" fill="#a9c6f6"/><path d="M8 46h6M11 43v6M52 10h6M55 7v6" stroke="#1f4fc1" stroke-width="2"/></svg>
  <span class="bar"></span><div><h3>Cleaning Done</h3><p>Lorem ipsum dolor sit amet, consectetur adipiscing elit,<br>sed do eiusmod tempor incididunt</p></div>
</div>

<!-- Testimonials -->
<div class="abs testi-bg"></div>
<h2 class="abs sec-title" style="top:2856px"><b>OUR</b> <span>TESTIMONIALS</span></h2>
<p class="abs sec-text" style="top:2921px">Lorem ipsum dolor sit amet, consectetur adipiscing elit, sed do eiusmod tempor incididunt ut labore et dolore magna aliqua. Quis ipsum suspendisse ultrices gravida.</p>

<div class="abs tcard" style="left:112px">
  <div class="head"><span class="quote">&ldquo;</span><span class="stars">★★★★★</span></div>
  <p>Lorem ipsum dolor sit amet, consectetur adipiscing elit, sed do eiusmod tempor incididunt ut labore et dolore magna aliqua. Quis ipsum suspendisse ultrices gravida. Risus commodo viverra maecenas accumsan</p>
  <div class="person"><div class="avatar">MQ</div><div><h4>Marla Quinn</h4><small>MD at Delta Groups</small></div></div>
</div>
<div class="abs tcard" style="left:452px">
  <div class="head"><span class="quote">&ldquo;</span><span class="stars">★★★★★</span></div>
  <p>Lorem ipsum dolor sit amet, consectetur adipiscing elit, sed do eiusmod tempor incididunt ut labore et dolore magna aliqua. Quis ipsum suspendisse ultrices gravida. Risus commodo viverra maecenas accumsan</p>
  <div class="person"><div class="avatar">MQ</div><div><h4>Marla Quinn</h4><small>MD at Delta Groups</small></div></div>
</div>
<div class="abs tcard" style="left:792px">
  <div class="head"><span class="quote">&ldquo;</span><span class="stars">★★★★★</span></div>
  <p>Lorem ipsum dolor sit amet, consectetur adipiscing elit, sed do eiusmod tempor incididunt ut labore et dolore magna aliqua. Quis ipsum suspendisse ultrices gravida. Risus commodo viverra maecenas accumsan</p>
  <div class="person"><div class="avatar">MQ</div><div><h4>Marla Quinn</h4><small>MD at Delta Groups</small></div></div>
</div>
<div class="abs dots" style="top:3340px"><i class="on"></i><i></i><i></i><i></i></div>

<!-- Footer -->
<footer class="abs footer"></footer>
<div class="abs footer-brand">HARBOR TIDY TEAM</div>
<nav class="abs footer-nav"><span>Home</span><span>About</span><span>Services</span><span>Gallery</span><span>Testimonials</span><span>Contact Us</span></nav>
<div class="abs footer-line"></div>
<p class="abs copyright">Copyright © 2025 Harbor Tidy Team. All Rights Reserved.</p>

</body>
</html>
```